Dalvick's Business Card

I need some designs for a new business card including the new logo attached. An old example of our business card is also attached to show all the data that should be included on the new design.
**I added some more examples someone had mocked up**

Contact Information for Business Card

Should include all info on other examples uploaded.

```html
<!DOCTYPE html>
<html lang="en">
<head>
<meta charset="utf-8">
<title>Dalvick's Business Card</title>
<link href="https://fonts.googleapis.com/css2?family=Montserrat:wght@400;500;600;700;800&display=swap" rel="stylesheet">
<style>
  :root {
    --page: #d9d9d9;
    --card: #ffffff;
    --card-back: #f1f1f1;
    --blue: #0b6fb5;
    --blue-light: #4a98cf;
    --red: #e0313f;
    --red-deep: #b80f1d;
    --white: #ffffff;
  }
  * { margin: 0; padding: 0; box-sizing: border-box; }
  html, body {
    width: 1200px; height: 1200px; overflow: hidden;
    background: var(--page);
    font-family: "Montserrat", sans-serif;
  }
  .sheet {
    position: relative; width: 1200px; height: 1200px;
    display: flex; flex-direction: column; align-items: center; justify-content: center; gap: 60px;
  }
  .card {
    position: relative; width: 840px; height: 480px;
    border-radius: 28px; overflow: hidden;
    background: var(--card);
    box-shadow: 0 10px 24px rgba(0,0,0,0.18);
  }
  .card--back { background: var(--card-back); }
  .card svg.decor { position: absolute; inset: 0; width: 100%; height: 100%; }

  /* wordmark */
  .wordmark { display: flex; align-items: center; gap: 18px; }
  .wordmark__dot { border-radius: 50%; background: var(--blue); flex: none; }
  .wordmark__name { color: var(--blue); font-weight: 700; line-height: 1; letter-spacing: 1px; white-space: nowrap; }
  .tagline { color: var(--red); font-weight: 700; text-transform: uppercase; letter-spacing: 1px; white-space: nowrap; }
  .service-area { color: var(--red); font-weight: 600; text-transform: uppercase; letter-spacing: 1px; white-space: nowrap; }

  /* front */
  .front-brand { position: absolute; left: 0; right: 0; top: 120px; display: flex; flex-direction: column; align-items: center; }
  .front-brand .service-area { font-size: 15px; margin-bottom: 12px; }
  .front-brand .wordmark__dot { width: 70px; height: 70px; }
  .front-brand .wordmark__name { font-size: 86px; }
  .front-brand .tagline { font-size: 21px; margin-top: 12px; }
  .front-slogan {
    position: absolute; left: 0; right: 0; bottom: 30px; text-align: center; white-space: nowrap;
    color: var(--white); font-size: 18px; font-weight: 500; letter-spacing: 2px; text-transform: uppercase;
  }

  /* back */
  .person-name {
    position: absolute; left: 70px; top: 88px; white-space: nowrap;
    color: var(--red); font-size: 44px; font-weight: 800; letter-spacing: 1px; text-transform: uppercase;
  }
  .badge-label {
    position: absolute; left: 592px; top: 111px; width: 223px; text-align: center; white-space: nowrap;
    color: var(--white); font-size: 16px; font-weight: 500; letter-spacing: 1.5px; text-transform: uppercase;
  }
  .back-brand { position: absolute; right: 40px; top: 185px; display: flex; flex-direction: column; align-items: flex-start; }
  .back-brand .wordmark { gap: 12px; }
  .back-brand .wordmark__dot { width: 42px; height: 42px; }
  .back-brand .wordmark__name { font-size: 54px; }
  .back-brand .tagline { font-size: 13px; margin-top: 8px; margin-left: 54px; }
  .contact-list { position: absolute; left: 70px; top: 255px; list-style: none; }
  .contact-list li {
    display: flex; align-items: center; gap: 14px; white-space: nowrap;
    color: var(--blue); font-size: 26px; font-weight: 400; margin-bottom: 8px;
  }
  .contact-list svg { width: 22px; height: 22px; fill: var(--red); flex: none; }
  .back-slogan {
    position: absolute; right: 40px; bottom: 34px; white-space: nowrap;
    color: var(--white); font-size: 20px; font-weight: 500; letter-spacing: 2px; text-transform: uppercase;
  }
</style>
</head>
<body>
<main class="sheet">

  <section class="card card--front">
    <svg class="decor" viewBox="0 0 840 480" aria-hidden="true">
      <defs>
        <linearGradient id="band-front" x1="0" x2="1" y1="0" y2="0">
          <stop offset="0" stop-color="#4a98cf"/>
          <stop offset="1" stop-color="#0b6fb5"/>
        </linearGradient>
      </defs>
      <path d="M0 400 H350 L385 360 L425 380 H840 V480 H0 Z" fill="url(#band-front)"/>
    </svg>
    <div class="front-brand">
      <p class="service-area">Serves Fairmont Ridge &amp; surrounding areas</p>
      <div class="wordmark">
        <span class="wordmark__dot"></span>
        <span class="wordmark__name">DALVICK'S</span>
      </div>
      <p class="tagline">Air Conditioning &amp; Heating Service</p>
    </div>
    <p class="front-slogan">Call today for all your HVAC, refrigeration &amp; plumbing needs</p>
  </section>

  <section class="card card--back">
    <svg class="decor" viewBox="0 0 840 480" aria-hidden="true">
      <defs>
        <linearGradient id="rule" x1="0" x2="1">
          <stop offset="0" stop-color="#4a98cf"/>
          <stop offset="1" stop-color="#0b6fb5"/>
        </linearGradient>
        <linearGradient id="swoosh-red" x1="0" x2="1">
          <stop offset="0" stop-color="#b80f1d"/>
          <stop offset="1" stop-color="#e0313f"/>
        </linearGradient>
      </defs>
      <rect x="70" y="148" width="500" height="3" fill="url(#rule)"/>
      <path d="M550 151 L592 92 H815 V151 Z" fill="#0b6fb5"/>
      <path d="M0 480 C140 430 290 395 460 385 C310 405 210 440 140 480 Z" fill="url(#swoosh-red)"/>
      <path d="M180 480 C380 410 600 365 840 345 V480 Z" fill="#0b6fb5"/>
    </svg>

    <h1 class="person-name">Mark Dalvick</h1>
    <p class="badge-label">Licensed &amp; Insured</p>

    <div class="back-brand">
      <div class="wordmark">
        <span class="wordmark__dot"></span>
        <span class="wordmark__name">DALVICK'S</span>
      </div>
      <p class="tagline">Air Conditioning &amp; Heating Service</p>
    </div>

    <ul class="contact-list">
      <li>
        <svg viewBox="0 0 24 24" aria-hidden="true"><path d="M6.6 10.8a15.1 15.1 0 0 0 6.6 6.6l2.2-2.2a1 1 0 0 1 1-.25 11.4 11.4 0 0 0 3.6.57 1 1 0 0 1 1 1V20a1 1 0 0 1-1 1A17 17 0 0 1 3 4a1 1 0 0 1 1-1h3.5a1 1 0 0 1 1 1c0 1.25.2 2.45.57 3.6a1 1 0 0 1-.25 1Z"/></svg>
        <span>555.014.2290</span>
      </li>
      <li>
        <svg viewBox="0 0 24 24" aria-hidden="true"><path d="M2 5h20v14H2Zm2 2v.5l8 5 8-5V7Z"/></svg>
        <span>service@dalvickhvac.com</span>
      </li>
    </ul>

    <p class="back-slogan">Family owned &amp; operated</p>
  </section>

</main>
</body>
</html>
```